New Zealand Marlborough Sauvignon Blanc wine packaging design

We need packaging design for our new wine brand, Dunmore Vale. The wine is a New Zealand Marlborough Sauvignon Blanc. We would like the packaging will portray elegance and style with an understated label. We are looking for a label that portrays the elegance of the French Riviera. The label should be round or pill shaped.
Updates

Industry/Entity Type

Wine

Font styles to use
Serif
Sans Serif

Requirements
Must have
• The words in order of importance: Dunmore Vale, Sauvignon Blanc, Marlborough, New Zealand. It should be fit to the bottle posted in the links
Nice to have
• a pill shape or circular shape
Should not have
• Illustrations of wine bottles, wine glasses, or grapes

```html
<!DOCTYPE html>
<html lang="en">
<head>
<meta charset="utf-8">
<title>Dunmore Vale – Marlborough Sauvignon Blanc Label</title>
<link rel="stylesheet" href="https://fonts.googleapis.com/css2?family=Cinzel:wght@400;600;700&family=Open+Sans:wght@400&display=swap">
<style>
  :root {
    --label-black: #2b2a27;
    --foil-orange: #f9a632;
    --cream: #fff8ea;
    --ink: #1a1a1a;
    --paper: #ffffff;
  }
  html, body {
    margin: 0;
    padding: 0;
    width: 1200px;
    height: 3000px;
    overflow: hidden;
    background: var(--paper);
  }
  .spec-sheet {
    position: relative;
    width: 1200px;
    height: 3000px;
  }
  .spec-drawing {
    position: absolute;
    left: 0;
    top: 0;
    width: 1200px;
    height: 1100px;
  }
  .dimension-line { stroke: var(--ink); stroke-width: 1.4; fill: none; }
  .dimension-arrow { fill: var(--ink); }
  .dimension-text {
    font-family: "Open Sans", sans-serif;
    font-size: 22px;
    fill: var(--ink);
  }
  .label-ring { fill: var(--foil-orange); }
  .label-face { fill: var(--label-black); }
  .brand-name {
    font-family: "Cinzel", serif;
    font-weight: 700;
    font-size: 54px;
    fill: var(--paper);
  }
  .region-name {
    font-family: "Cinzel", serif;
    font-weight: 600;
    font-size: 30px;
    fill: var(--paper);
  }
  .country-name {
    font-family: "Cinzel", serif;
    font-size: 16px;
    fill: var(--foil-orange);
    letter-spacing: 2px;
  }
  .varietal-name {
    font-family: "Cinzel", serif;
    font-size: 44px;
    fill: var(--foil-orange);
  }
  .colour-legend {
    position: absolute;
    top: 1010px;
    left: 445px;
    display: flex;
    align-items: center;
    gap: 48px;
    font-family: "Open Sans", sans-serif;
    font-size: 35px;
    color: var(--ink);
  }
  .legend-item { display: flex; align-items: center; gap: 26px; }
  .legend-swatch { width: 27px; height: 33px; }
  .legend-swatch--black { background: var(--label-black); }
  .legend-swatch--foil { background: var(--foil-orange); }
</style>
</head>
<body>
<main class="spec-sheet">
  <svg class="spec-drawing" viewBox="0 0 1200 1100" xmlns="http://www.w3.org/2000/svg">
    <defs>
      <path id="arc-brand" d="M 433 559 A 176 176 0 0 1 785 559"/>
      <path id="arc-country" d="M 457 559 A 152 152 0 0 0 761 559"/>
      <path id="arc-region" d="M 425 559 A 184 184 0 0 0 793 559"/>
      <path id="arc-varietal" d="M 384 559 A 225 225 0 0 0 834 559"/>
      <radialGradient id="swirl-tone" cx="50%" cy="50%" r="50%">
        <stop offset="0%" stop-color="#f9a632"/>
        <stop offset="55%" stop-color="#c98228"/>
        <stop offset="100%" stop-color="#3a3128"/>
      </radialGradient>
    </defs>

    <g class="dimension dimension--width">
      <line class="dimension-line" x1="364" y1="245" x2="364" y2="337"/>
      <line class="dimension-line" x1="858" y1="245" x2="858" y2="337"/>
      <line class="dimension-line" x1="372" y1="257" x2="850" y2="257"/>
      <polygon class="dimension-arrow" points="364,257 376,252 376,262"/>
      <polygon class="dimension-arrow" points="858,257 846,252 846,262"/>
      <text class="dimension-text" x="602" y="242" text-anchor="middle">70mm</text>
    </g>

    <g class="dimension dimension--height">
      <line class="dimension-line" x1="305" y1="308" x2="395" y2="308"/>
      <line class="dimension-line" x1="305" y1="803" x2="395" y2="803"/>
      <line class="dimension-line" x1="316" y1="316" x2="316" y2="795"/>
      <polygon class="dimension-arrow" points="316,308 311,320 321,320"/>
      <polygon class="dimension-arrow" points="316,803 311,791 321,791"/>
      <text class="dimension-text" x="300" y="563" text-anchor="middle" transform="rotate(-90 300 563)">70mm</text>
    </g>

    <g class="wine-label">
      <circle class="label-ring" cx="609" cy="559" r="252"/>
      <circle class="label-face" cx="609" cy="559" r="240"/>

      <circle class="swirl-artwork" cx="609" cy="545" r="132" fill="url(#swirl-tone)"
              role="img" aria-label="Brushed gold swirl motif"/>

      <ellipse class="blossom-spray blossom-spray--left" cx="458" cy="608" rx="56" ry="36"
               fill="var(--cream)" opacity="0.92"
               role="img" aria-label="Spray of white blossoms"/>
      <ellipse class="blossom-spray blossom-spray--right" cx="763" cy="618" rx="56" ry="38"
               fill="var(--cream)" opacity="0.92"
               role="img" aria-label="Spray of white blossoms"/>

      <text class="brand-name"><textPath href="#arc-brand" startOffset="50%" text-anchor="middle" textLength="520" lengthAdjust="spacing">DUNMORE VALE</textPath></text>
      <text class="country-name"><textPath href="#arc-country" startOffset="50%" text-anchor="middle">NEW ZEALAND</textPath></text>
      <text class="region-name"><textPath href="#arc-region" startOffset="50%" text-anchor="middle">MARLBOROUGH</textPath></text>
      <text class="varietal-name"><textPath href="#arc-varietal" startOffset="50%" text-anchor="middle">SAUVIGNON BLANC</textPath></text>
    </g>
  </svg>

  <div class="colour-legend">
    <div class="legend-item"><span class="legend-swatch legend-swatch--black"></span><span>BLACK</span></div>
    <div class="legend-item"><span class="legend-swatch legend-swatch--foil"></span><span>FOLGE</span></div>
  </div>
</main>
</body>
</html>
```